Fizz's Shed & Grill Burger Restaurant Website - HomePage Only PSD

I need a website design for a restaurant called "Fizz's Shed and Grill" featuring burgers, wings, beer, live music, trivia, and more. I have several images of the restaurant and they already have their logo files created (see attached). I want some type of wood background and integrate the silver tin. This needs to be a modern, hip and fun type design. Design must incorporate these attached graphics.

UPDATE - just added a few more images of things I really like to be incorporated into my designs.
Updates

Industry/Entity Type

Burger Restaurant

Number of Pages Required

1 page

Font styles to use
Sans Serif

Requirements
Must have
• Restaurant/Bar theme with integration of existing logo and the red wood look.
Nice to have
• - Modern Fun appearance
• - Use Pelko Fonts

```html
<!DOCTYPE html>
<html lang="en">
<head>
<meta charset="utf-8">
<title>Fizz's Shed and Grill</title>
<link href="https://fonts.googleapis.com/css2?family=Kalam:wght@400;700&family=Lato:wght@400;700;900&display=swap" rel="stylesheet">
<style>
:root{
  --dark:#2b1a0b;
  --brown:#3d2510;
  --gold:#bf864a;
  --gold-text:#d39552;
  --cream:#f6efe4;
  --white:#ffffff;
  --line:rgba(255,255,255,.3);
  --ink:#2b1a0b;
}
*{box-sizing:border-box;margin:0;padding:0}
html,body{width:1200px;height:2736px;overflow:hidden}
body{position:relative;font-family:"Lato",sans-serif;color:var(--white);background:var(--dark)}
.abs{position:absolute}
.wood{background:
  repeating-linear-gradient(90deg,rgba(95,55,22,.28) 0 2px,transparent 2px 387px),
  radial-gradient(ellipse 26px 90px at 22% 30%,rgba(120,68,28,.28),transparent 70%),
  radial-gradient(ellipse 30px 110px at 63% 70%,rgba(120,68,28,.25),transparent 70%),
  radial-gradient(ellipse 22px 80px at 86% 22%,rgba(120,68,28,.22),transparent 70%),
  repeating-linear-gradient(91deg,rgba(255,232,195,.09) 0 4px,transparent 4px 13px,rgba(115,64,26,.09) 13px 15px,transparent 15px 29px),
  repeating-linear-gradient(89deg,rgba(120,70,30,.07) 0 1px,transparent 1px 6px),
  linear-gradient(90deg,#c6925b,#dcae77 14%,#c98f55 31%,#d8a96f 47%,#c28a52 62%,#ddb07a 78%,#c8935b)}
.wood-h{background:
  repeating-linear-gradient(0deg,rgba(255,228,190,.08) 0 3px,transparent 3px 9px,rgba(100,55,20,.12) 9px 11px,transparent 11px 19px),
  repeating-linear-gradient(2deg,rgba(90,50,20,.08) 0 1px,transparent 1px 5px),
  linear-gradient(90deg,#b98350,#cf9f68 25%,#b47c48 50%,#d1a26c 75%,#ba8550)}
.hand{font-family:"Kalam",cursive;font-weight:400;text-transform:uppercase}
.btn{position:absolute;background:var(--gold);color:var(--white);font-weight:700;font-size:16px;display:flex;align-items:center;justify-content:center}

.topbar{left:0;top:0;width:1200px;height:55px;background:var(--dark);font-size:14px;font-weight:700}
.topbar span{position:absolute;top:18px}
.social-dot{position:absolute;top:13px;width:29px;height:29px;border:1.5px solid var(--gold);border-radius:50%}

.header{left:0;top:55px;width:1200px;height:105px;box-shadow:0 2px 4px rgba(0,0,0,.3)}
.brand{left:100px;top:55px;width:200px;height:137px;background:var(--cream);clip-path:polygon(0 0,100% 0,100% 85%,50% 100%,0 85%);display:flex;flex-direction:column;align-items:center;justify-content:center;z-index:3;color:var(--brown);font-family:"Kalam",cursive;font-weight:700;font-size:20px;line-height:1.05;text-align:center;padding-bottom:12px}
.brand i{display:block;width:30px;height:30px;border-radius:50%;background:var(--brown);margin-bottom:6px}
.nav{top:98px;font-family:"Kalam",cursive;font-size:16px;color:var(--white);text-transform:uppercase;letter-spacing:.5px;text-shadow:0 1px 2px rgba(0,0,0,.35)}
.nav.active{color:var(--dark);text-shadow:none}
.nav.active::after{content:"";position:absolute;left:50%;top:44px;width:16px;height:8px;margin-left:-8px;background:var(--dark);border-radius:8px 8px 0 0}

.hero{left:0;top:160px;width:1200px;height:515px;background:
  radial-gradient(ellipse 330px 120px at 740px 130px,#e9a64e 0,rgba(233,166,78,0) 100%),
  radial-gradient(ellipse 360px 110px at 690px 330px,#b8602a 0,rgba(184,96,42,0) 100%),
  radial-gradient(ellipse 220px 90px at 880px 260px,#a0151b 0,rgba(160,21,27,0) 100%),
  radial-gradient(ellipse 220px 170px at 140px 120px,#5f9a2a 0,rgba(95,154,42,0) 100%),
  radial-gradient(ellipse 280px 180px at 200px 410px,#eec14a 0,rgba(238,193,74,0) 100%),
  radial-gradient(ellipse 200px 120px at 1080px 280px,#5c8f2a 0,rgba(92,143,42,0) 100%),
  linear-gradient(180deg,#7a3a14,#4d230c 60%,#8a5a32)}
.hero-title{left:374px;top:378px;width:446px;height:62px;background:rgba(0,0,0,.3);font-weight:700;font-size:35px;display:flex;align-items:center;justify-content:center;text-shadow:0 2px 3px rgba(0,0,0,.4)}
.arrow{top:378px;width:40px;height:34px;background:rgba(0,0,0,.7);display:flex;align-items:center;justify-content:center}

.band{left:0;top:675px;width:1200px;height:328px}
.card{top:607px;width:307px;height:354px;background:var(--white);box-shadow:0 4px 10px rgba(0,0,0,.35);color:#222;text-align:center}
.card .pic{position:absolute;left:8px;top:7px;width:291px;height:165px}
.card h3{position:absolute;left:0;right:0;top:184px;font-family:"Kalam",cursive;font-size:21px;font-weight:400;color:var(--gold-text)}
.card p{position:absolute;left:12px;right:12px;top:225px;font-size:13px;line-height:20px}
.card .btn{left:99px;top:298px;width:110px;height:33px}

.welcome{left:0;top:1003px;width:1200px;height:401px;background:radial-gradient(ellipse 500px 300px at 20% 40%,#4a2e14,transparent),var(--brown)}
.sec-title{left:0;width:1200px;text-align:center;font-size:31px;letter-spacing:1.5px}
.rule{height:1px;background:var(--line)}
.emblem{width:32px;height:32px;border-radius:50%;border:2px solid var(--white);background:var(--brown)}
.lead{left:100px;top:1138px;font-size:19px}
.body-copy{left:100px;top:1180px;width:548px;font-size:13.5px;line-height:27.5px;color:#e8d9c6}

.gallery{left:0;top:1404px;width:1200px;height:570px}
.ph{box-shadow:inset 0 0 0 8px rgba(0,0,0,.12),inset 0 0 0 9px rgba(255,255,255,.55)}

.lower{left:0;top:1974px;width:1200px;height:458px;background:
  radial-gradient(circle 8px at 180px 2240px,rgba(255,200,120,.35),transparent),
  radial-gradient(ellipse 240px 70px at 300px 120px,rgba(120,85,55,.45),transparent),
  radial-gradient(ellipse 260px 80px at 880px 90px,rgba(110,80,50,.4),transparent),
  radial-gradient(ellipse 300px 90px at 560px 250px,rgba(90,65,40,.4),transparent),
  repeating-linear-gradient(8deg,rgba(255,255,255,.025) 0 14px,transparent 14px 60px),
  radial-gradient(ellipse at 50% 40%,#32251a 0,#120d09 75%)}
.field{left:755px;width:347px;height:37px;border:1px solid rgba(255,255,255,.55);font-size:15px;font-weight:700;display:flex;align-items:center;padding-left:44px}
.field svg{position:absolute;left:10px;top:10px}
.field::before{content:"";position:absolute;left:34px;top:0;bottom:0;width:1px;background:rgba(255,255,255,.35)}
.quote{left:150px;top:2270px;width:500px;text-align:center;font-size:14px;line-height:26px;color:#ddd}

.footer{left:0;top:2432px;width:1200px;height:253px}
.fh{font-family:"Kalam",cursive;font-size:14px;font-weight:400;text-transform:uppercase;color:var(--ink);top:2470px;letter-spacing:.5px}
.fl{font-size:14px;font-weight:700;color:var(--ink);line-height:23px}
.copy{left:0;top:2685px;width:1200px;height:51px;background:var(--dark);font-size:14px;font-weight:700;display:flex;align-items:center;justify-content:center}
.soc{display:inline-block;width:26px;height:26px;border-radius:50%;background:#fff;vertical-align:middle;margin-right:10px}
</style>
</head>
<body>

<div class="abs topbar">
  <svg class="abs" style="left:100px;top:20px" width="14" height="14" viewBox="0 0 14 14"><path d="M3 1l3 3-2 2c1 2 2 3 4 4l2-2 3 3-2 2C6 13 1 8 1 3z" fill="#bf864a"/></svg>
  <span style="left:122px">123 - 456 - 789</span>
  <svg class="abs" style="left:256px;top:21px" width="16" height="12" viewBox="0 0 16 12"><rect x="0.5" y="0.5" width="15" height="11" fill="#bf864a"/><path d="M1 1l7 6 7-6" stroke="#2b1a0b" fill="none"/></svg>
  <span style="left:278px">info@fizzshed.com</span>
  <i class="social-dot" style="left:947px"></i><i class="social-dot" style="left:988px"></i><i class="social-dot" style="left:1029px"></i><i class="social-dot" style="left:1070px"></i>
</div>

<div class="abs header wood-h"></div>
<div class="abs brand"><i></i>Fizz's Shed<br>and Grill</div>
<span class="abs nav active" style="left:487px">Home</span>
<span class="abs nav" style="left:571px">Restaurant</span>
<span class="abs nav" style="left:715px">Bar</span>
<span class="abs nav" style="left:790px">Events</span>
<span class="abs nav" style="left:896px">Gallery</span>
<span class="abs nav" style="left:1005px">Contact Us</span>

<div class="abs hero" role="img" aria-label="Crispy chicken burger with fries and lettuce on a wooden table"></div>
<div class="abs hero-title">Best Burger In Town</div>
<div class="abs arrow" style="left:0"><svg width="12" height="14"><path d="M9 2L3 7l6 5" stroke="#fff" stroke-width="2.5" fill="none"/></svg></div>
<div class="abs arrow" style="left:1160px"><svg width="12" height="14"><path d="M3 2l6 5-6 5" stroke="#fff" stroke-width="2.5" fill="none"/></svg></div>

<div class="abs band wood"></div>
<div class="abs card" style="left:100px">
  <div class="pic" role="img" aria-label="Stacked double cheeseburger" style="background:radial-gradient(ellipse 110px 60px at 50% 30%,#e0a24a,transparent),radial-gradient(ellipse 100px 40px at 50% 70%,#6a3a14,transparent),linear-gradient(90deg,#9e0d18,#c01a22 50%,#8a0b14)"></div>
  <h3>FOOD</h3>
  <p>Lorem ipsum dolor sit amet, consectetur adipiscing elit, sed do eiusmod tempor incididunt ut labore et dolore magna aliqua. Ut enim</p>
  <div class="btn">Read More</div>
</div>
<div class="abs card" style="left:447px">
  <div class="pic" role="img" aria-label="Red cocktail on a bar counter" style="background:radial-gradient(ellipse 40px 30px at 28% 35%,#d0203a,transparent),radial-gradient(ellipse 150px 40px at 65% 55%,rgba(230,180,120,.45),transparent),linear-gradient(180deg,#1a1512,#2e221b 60%,#3a2a20)"></div>
  <h3>DRINK</h3>
  <p>Lorem ipsum dolor sit amet, consectetur adipiscing elit, sed do eiusmod tempor incididunt ut labore et dolore magna aliqua. Ut enim</p>
  <div class="btn">Read More</div>
</div>
<div class="abs card" style="left:793px">
  <div class="pic" role="img" aria-label="Hand playing an electric guitar" style="background:radial-gradient(ellipse 90px 70px at 35% 70%,#d09a78,transparent),radial-gradient(ellipse 80px 50px at 70% 35%,#8a5a3a,transparent),linear-gradient(135deg,#13245e,#2a3a8a 50%,#1a1430)"></div>
  <h3>MUSIC</h3>
  <p>Lorem ipsum dolor sit amet, consectetur adipiscing elit, sed do eiusmod tempor incididunt ut labore et dolore magna aliqua. Ut enim</p>
  <div class="btn">Read More</div>
</div>

<section class="abs welcome"></section>
<h2 class="abs sec-title hand" style="top:1030px">Welcome to Fizz's Shed and Grill</h2>
<div class="abs rule" style="left:298px;top:1101px;width:604px"></div>
<div class="abs emblem" style="left:584px;top:1085px"></div>
<p class="abs lead">Lorem ipsum dolor sit amet, consectetur adipiscing elit.</p>
<p class="abs body-copy">Sed ut perspiciatis unde omnis iste natus error sit voluptatem accusantium doloremque laudantium, totam rem aperiam, eaque ipsa quae ab illo inventore veritatis et quasi architecto beatae vitae dicta sunt explicabo. Nemo enim ipsam voluptatem quia voluptas sit aspernatur aut odit aut fugit, sed quia consequuntur magni dolores eos qui ratione voluptatem sequi nesciunt.</p>
<div class="btn" style="left:100px;top:1328px;width:110px;height:33px">Read More</div>
<div class="abs" role="img" aria-label="Restaurant exterior with wooden deck and pergola" style="left:689px;top:1131px;width:413px;height:230px;border:2px solid #ccc;background:radial-gradient(ellipse 120px 50px at 85% 45%,#6f8f4a,transparent),radial-gradient(ellipse 160px 70px at 35% 55%,#8a6a4a,transparent),radial-gradient(ellipse 90px 40px at 45% 25%,#9a2a28,transparent),linear-gradient(180deg,#7da6d8 0,#a8c2dc 25%,#6e6a58 55%,#5a5a40 80%,#8a8a70)"></div>

<section class="abs gallery wood"></section>
<h2 class="abs sec-title hand" style="top:1440px;color:var(--dark)">Photo Gallery</h2>
<div class="abs rule" style="left:480px;top:1512px;width:240px;background:rgba(43,26,11,.4)"></div>
<div class="abs emblem" style="left:584px;top:1496px;border-color:var(--dark);background:#d2a36c"></div>
<div class="abs ph" role="img" aria-label="Painted wooden flag on a barn wall" style="left:100px;top:1561px;width:367px;height:369px;background:radial-gradient(ellipse 70px 50px at 28% 42%,#2a3a6a,transparent),radial-gradient(ellipse 170px 110px at 50% 55%,#a8383a,transparent),linear-gradient(180deg,#2a221c,#5a4638 40%,#3a2e26 80%,#2a2420)"></div>
<div class="abs ph" role="img" aria-label="Tin sign on a wooden wall" style="left:476px;top:1561px;width:376px;height:190px;background:radial-gradient(ellipse 90px 40px at 55% 40%,#c8c48a,transparent),radial-gradient(ellipse 80px 30px at 75% 80%,#3a4a6a,transparent),linear-gradient(180deg,#7a5436,#5a3e28 60%,#3a2a1e)"></div>
<div class="abs ph" role="img" aria-label="Drink glass on a lit bar" style="left:476px;top:1757px;width:184px;height:173px;background:radial-gradient(circle 30px at 25% 30%,#e84a5a,transparent),radial-gradient(circle 30px at 70% 25%,#4ab07a,transparent),radial-gradient(ellipse 30px 50px at 60% 65%,#d8d8d0,transparent),linear-gradient(135deg,#6a1a2a,#2a1a22)"></div>
<div class="abs ph" role="img" aria-label="Round tin sign on a wood panel" style="left:666px;top:1757px;width:186px;height:173px;background:radial-gradient(circle 50px at 50% 45%,#a8a8a4,transparent),linear-gradient(180deg,#5a4634,#3a2c22)"></div>
<div class="abs ph" role="img" aria-label="Interior with string lights and wood beams" style="left:861px;top:1561px;width:241px;height:369px;background:radial-gradient(ellipse 110px 18px at 50% 15%,rgba(255,210,130,.5),transparent),radial-gradient(ellipse 110px 18px at 50% 40%,rgba(255,210,130,.45),transparent),radial-gradient(ellipse 60px 35px at 50% 80%,#2a6a6a,transparent),linear-gradient(180deg,#2a2420,#5a4636 45%,#3a302a 70%,#2a2a2a)"></div>

<section class="abs lower" role="img" aria-label="Softly blurred bar interior with warm lights"></section>
<h2 class="abs hand" style="left:100px;top:2010px;font-size:31px;letter-spacing:1px">Happy Customers</h2>
<div class="abs rule" style="left:100px;top:2074px;width:500px"></div>
<div class="abs emblem" style="left:100px;top:2058px;background:#1a140e"></div>
<svg class="abs" style="left:556px;top:2044px" width="42" height="18"><circle cx="9" cy="9" r="8" stroke="#fff" fill="none"/><path d="M11 5l-4 4 4 4" stroke="#fff" fill="none"/><circle cx="33" cy="9" r="8" stroke="#fff" fill="none"/><path d="M31 5l4 4-4 4" stroke="#fff" fill="none"/></svg>
<div class="abs" role="img" aria-label="Customer portrait" style="left:330px;top:2117px;width:132px;height:132px;border-radius:50%;border:4px solid #fff;background:radial-gradient(circle at 50% 45%,#c8a088 0,#9a7a68 40%,#d8d8d8 70%)"></div>
<p class="abs quote"><b style="font-family:Georgia,serif;font-size:30px;color:#999;vertical-align:-8px">&ldquo;</b> Duis autem vel eum iriure dolor in hendrerit in vulputate velitj esse molestie consequat, vel illum dolore eu feugiat nulla faciln sis at vero eros et accumsan et delenit facilisi. <b style="font-family:Georgia,serif;font-size:30px;color:#999;vertical-align:-14px">&rdquo;</b></p>
<p class="abs" style="left:150px;top:2367px;width:500px;text-align:center;font-weight:700;font-size:16px">Mr. Ravi Menon</p>
<div class="abs" style="left:685px;top:2070px;width:0;height:305px;border-left:1px dashed rgba(255,255,255,.6)"></div>

<h2 class="abs hand" style="left:744px;top:2010px;font-size:31px;letter-spacing:1px">Book Your Table</h2>
<div class="abs rule" style="left:744px;top:2074px;width:358px"></div>
<div class="abs emblem" style="left:744px;top:2058px;background:#1a140e"></div>
<div class="abs field" style="top:2118px"><svg width="16" height="16"><circle cx="8" cy="8" r="7" fill="#ddd"/><rect x="7" y="7" width="2" height="5" fill="#111"/><rect x="7" y="4" width="2" height="2" fill="#111"/></svg>Name :</div>
<div class="abs field" style="top:2165px"><svg width="16" height="16"><rect x="1" y="3" width="14" height="10" stroke="#ddd" fill="none"/><path d="M1 3l7 6 7-6" stroke="#ddd" fill="none"/></svg>Email :</div>
<div class="abs field" style="top:2212px"><svg width="16" height="16" viewBox="0 0 14 14"><path d="M3 1l3 3-2 2c1 2 2 3 4 4l2-2 3 3-2 2C6 13 1 8 1 3z" fill="#ddd"/></svg>Phone :</div>
<div class="abs field" style="top:2259px"><svg width="16" height="16"><rect x="1" y="2" width="14" height="13" stroke="#ddd" fill="none"/><path d="M1 6h14M5 0v4M11 0v4" stroke="#ddd"/></svg>Date :</div>
<div class="abs field" style="top:2306px"><svg width="16" height="16"><circle cx="8" cy="8" r="7" stroke="#ddd" fill="none"/><path d="M8 4v4h3" stroke="#ddd" fill="none"/></svg>Time :</div>
<div class="btn" style="left:755px;top:2353px;width:113px;height:33px">Submit</div>

<footer class="abs footer wood"></footer>
<p class="abs fh" style="left:100px">Quick Links</p>
<ul class="abs fl" style="left:100px;top:2496px;list-style:none">
  <li>› &nbsp;Home</li><li>› &nbsp;Restaurant</li><li>› &nbsp;Bar</li><li>› &nbsp;Events</li><li>› &nbsp;Gallery</li><li>› &nbsp;Contact us</li>
</ul>
<p class="abs fh" style="left:270px">Opening Hours</p>
<p class="abs fl" style="left:270px;top:2496px">Monday - Sunday<br>10:00 am - 11:00 pm</p>
<p class="abs fh" style="left:270px;top:2548px">Address</p>
<p class="abs fl" style="left:270px;top:2572px">123, Lorem ipsum dolor sit<br>amet, consectetuer,</p>
<p class="abs fl" style="left:270px;top:2620px;font-size:15px">Ph. 123 456 7890</p>
<p class="abs fh" style="left:487px">Location Map</p>
<div class="abs" role="img" aria-label="Street map of the restaurant area with location pin" style="left:487px;top:2512px;width:181px;height:124px;border:2px solid #fff;background:radial-gradient(ellipse 50px 30px at 30% 60%,#9ec0e0,transparent),radial-gradient(ellipse 60px 25px at 70% 30%,#a8c8e4,transparent),linear-gradient(135deg,#efe8d8,#e6dcc2 50%,#f0eadc)"></div>
<p class="abs fh" style="left:746px">Follow Us</p>
<div class="abs fl" style="left:746px;top:2505px;font-size:12px;line-height:34px">
  <div><i class="soc"></i>FRIENDPAGE</div>
  <div><i class="soc"></i>CHIRPER</div>
  <div><i class="soc"></i>SNAPGRAM</div>
  <div><i class="soc"></i>CIRCLES+</div>
</div>
<div class="abs" style="left:926px;top:2475px;width:176px;height:176px;border-radius:50%;border:3px solid #fff;display:flex;align-items:center;justify-content:center;text-align:center;font-family:'Kalam',cursive;font-weight:700;font-size:24px;line-height:1.1;color:#fff">Fizz's Shed<br>and Grill</div>

<div class="abs copy">Copyright © 2016 Fizz's Shed and Grill. All Right Reserved</div>

</body>
</html>
```